Parcelwise HQ letterhead and envelope

Design a formal (8.5x11) letterhead and envelope for sales outreach and legal matters. Using design input from https://www.parcelwisehq.example/ and the attached documents.

Industry/Entity Type

Software Service

Requirements
Must have
• These 4 hex colors are our official colors:
• #355c98 [blue]
• #1eb1a2 [teal]
• #fdba12 [gold]
• #f1653b [orange]
• So no other colors besides these should be used.

```html
<!DOCTYPE html>
<html lang="en">
<head>
<meta charset="utf-8">
<title>Parcelwise HQ letterhead and envelope</title>
<link rel="stylesheet" href="https://fonts.googleapis.com/css2?family=Open+Sans:wght@300;400;700&display=swap">
<style>
  :root {
    --blue: #355c98;
    --gold: #fdba12;
    --paper: #f6f6f7;
    --stage: #e4e5e7;
    --body-text: #7a7a7a;
    --white: #ffffff;
  }
  * { box-sizing: border-box; margin: 0; padding: 0; }
  html, body { width: 1200px; height: 825px; overflow: hidden; }
  body {
    background: var(--stage);
    font-family: "Open Sans", Arial, sans-serif;
    position: relative;
  }

  /* Letterhead sheet */
  .letterhead {
    position: absolute;
    left: 81px; top: 83px;
    width: 465px; height: 658px;
    background: var(--paper);
    overflow: hidden;
  }
  .brand {
    position: absolute;
    display: flex; align-items: center; gap: 7px;
    color: var(--blue);
    font-weight: 300;
    font-size: 19px;
    letter-spacing: 0.2px;
    white-space: nowrap;
  }
  .brand-mark {
    width: 24px; height: 24px;
    border: 2px solid var(--blue);
    border-radius: 50%;
  }
  .letterhead .brand { left: 30px; top: 27px; }

  .contact-block {
    position: absolute;
    left: 334px; top: 28px;
    border-left: 1px solid #d0d0d0;
    padding-left: 5px;
    font-size: 7px;
    line-height: 9px;
    color: #555;
  }
  .contact-block li { list-style: none; display: flex; align-items: center; gap: 3px; }
  .contact-dot {
    width: 6px; height: 6px; border-radius: 50%;
    background: var(--blue);
    display: inline-block;
  }

  .salutation {
    position: absolute;
    left: 38px; top: 135px;
    font-family: Arial, "Open Sans", sans-serif;
    font-weight: 700;
    font-size: 10.5px;
    color: var(--blue);
  }
  .letter-body {
    position: absolute;
    left: 38px; top: 162px;
    width: 390px;
    font-size: 8.8px;
    line-height: 12.2px;
    color: var(--body-text);
    text-align: justify;
  }
  .letter-body p { margin-bottom: 12.2px; }

  .signature {
    position: absolute;
    left: 38px; top: 457px;
    width: 88px; height: 44px;
    background: linear-gradient(100deg, #d9d9d9, #c4c4c4);
    border-radius: 3px;
  }

  /* Footer band: plain blue strip with a gold rule above */
  .footer-band {
    position: absolute;
    left: 0; bottom: 0;
    width: 100%; height: 30px;
    background: var(--blue);
  }
  .footer-rule {
    position: absolute;
    left: 0; bottom: 34px;
    width: 100%; height: 3px;
    background: var(--gold);
  }
  .footer-address {
    position: absolute;
    bottom: 10px;
    display: flex; align-items: center; gap: 4px;
    font-size: 8.8px;
    color: var(--white);
    white-space: nowrap;
  }
  .letterhead .footer-address { left: 274px; }

  /* Envelope */
  .envelope {
    position: absolute;
    left: 582px; top: 444px;
    width: 534px; height: 297px;
  }
  .envelope-flap {
    position: absolute; left: 0; top: 0;
    width: 534px; height: 65px;
    display: block;
  }
  .flap-url {
    position: absolute;
    left: 0; right: 0; top: 26px;
    text-align: center;
    font-size: 7px;
    letter-spacing: 3px;
    color: var(--blue);
    transform: rotate(180deg);
  }
  .envelope-body {
    position: absolute;
    left: 0; top: 64px;
    width: 534px; height: 233px;
    background: var(--paper);
    border-top: 1px dotted #cfcfcf;
    overflow: hidden;
  }
  .envelope .brand { left: 34px; top: 8px; }
  .address-window {
    position: absolute;
    left: 34px; top: 116px;
    width: 206px; height: 60px;
    background: #f3f3f4;
    border-radius: 4px;
    padding: 15px 8px 0;
  }
  .address-window span {
    display: block;
    border-bottom: 1px dotted #b9b9b9;
    height: 11px;
  }
  .envelope .footer-address { left: 345px; }
</style>
</head>
<body>

<section class="letterhead">
  <div class="brand"><span class="brand-mark"></span>Parcelwise HQ</div>

  <ul class="contact-block">
    <li><span class="contact-dot"></span>(800) 555-0142</li>
    <li><span class="contact-dot"></span>jsmith@parcelwisehq.example</li>
    <li><span class="contact-dot"></span>www.parcelwisehq.example</li>
  </ul>

  <h1 class="salutation">Dear Mr. Ellison,</h1>

  <div class="letter-body">
    <p>Lorem Ipsum is simply dummy text of the printing and typesetting industry. Lorem Ipsum has been the industry's standard dummy text ever since the 1500s, when an unknown printer took a galley of type and scrambled it to make a type specimen book. It has survived not only five centuries, but also the leap into electronic typesetting, remaining essentially unchanged.</p>
    <p>The standard chunk of Lorem Ipsum used since the 1500s is reproduced below for those interested. Sections 1.10.32 and 1.10.33 from "de Finibus Bonorum et Malorum" by Marcus are also reproduced in their exact original form, accompanied by English versions from the 1914 translation by H. Whitford</p>
    <p>Lorem Ipsum is simply dummy text of the printing and typesetting industry. Lorem Ipsum has been the industry's standard dummy text ever since the 1500s, when an unknown printer took a galley of type and scrambled it to make a type specimen book. It has survived not only five centuries, but also the leap into electronic typesetting, remaining essentially unchanged. It was popularised in the</p>
    <p>Lorem Ipsum is simply dummy text of the printing and typesetting industry. Lorem Ipsum has been the industry's standard dummy text ever since the 1500s, when an unknown printer took a galley of type and scrambled it to make a type specimen book. It has survived not only five centuries, but also the leap into electronic typesetting, remaining essentially unchanged. It was popularised in the</p>
  </div>

  <div class="signature" role="img" aria-label="Handwritten signature of the sender"></div>

  <div class="footer-rule"></div>
  <div class="footer-band"></div>
  <div class="footer-address">
    <svg width="7" height="10" viewBox="0 0 7 10" aria-hidden="true"><path fill="var(--gold)" d="M3.5,0 A3.5,3.5 0 0 1 7,3.5 C7,6 3.5,10 3.5,10 C3.5,10 0,6 0,3.5 A3.5,3.5 0 0 1 3.5,0 Z M3.5,2 A1.4,1.4 0 1 0 3.5,4.8 A1.4,1.4 0 1 0 3.5,2 Z"/></svg>
    212 Harbor Lane Fairview, MI 49999
  </div>
</section>

<section class="envelope">
  <svg class="envelope-flap" viewBox="0 0 534 65" aria-hidden="true">
    <path fill="var(--paper)" d="M10,10 Q12,0 22,0 L512,0 Q522,0 524,10 L534,65 L0,65 Z"/>
  </svg>
  <div class="flap-url">www.parcelwisehq.example</div>

  <div class="envelope-body">
    <div class="brand"><span class="brand-mark"></span>Parcelwise HQ</div>
    <div class="address-window"><span></span><span></span><span></span></div>

    <div class="footer-rule"></div>
    <div class="footer-band"></div>
    <div class="footer-address">
      <svg width="7" height="10" viewBox="0 0 7 10" aria-hidden="true"><path fill="var(--gold)" d="M3.5,0 A3.5,3.5 0 0 1 7,3.5 C7,6 3.5,10 3.5,10 C3.5,10 0,6 0,3.5 A3.5,3.5 0 0 1 3.5,0 Z M3.5,2 A1.4,1.4 0 1 0 3.5,4.8 A1.4,1.4 0 1 0 3.5,2 Z"/></svg>
      212 Harbor Lane Fairview, MI 49999
    </div>
  </div>
</section>

</body>
</html>
```